I want ideas sample designs for my book cover

Hello,

We need a book cover designed in flat and 3D Versions. We would like to have jpg and png for final output and include a copy of the PSD for future revisions.

Here are the basic details:

Title: The Harvest of Quiet Builders
Author: Norman Quillfeather

Dimensions of book:

Was looking at the Pavo website for dimensions. I thought you may want to go on there and look at the different sizes. I used the 6x9” perfect bound US trade size for my book. You will see that this has a spine width of 0.225”, Cover size of 12.48 x 9.25” and spine begins at 6.125”

If you need background info on the author just to get an idea what he does, please check:

http://NormanQuillfeather.example

IMPORTANT: Please see attached document for a more detailed info:

Exact Title Of book
Back Cover
Spine Info
Measurements of book and dimension
Examples of book covers
Norman's photo attached

Thanks,
Darlene

Industry/Entity Type

Life Coaching

Font styles to use
Serif

Requirements
Must have
• Jpg, png and PSD files
• title
• author
• exact dimensions
• front and back cover
• flat and 3d versions

```html
<!DOCTYPE html>
<html lang="en">
<head>
<meta charset="utf-8">
<title>The Harvest of Quiet Builders – Cover Spread</title>
<link rel="stylesheet" href="https://fonts.googleapis.com/css2?family=Tinos:wght@400;700&family=Arimo:wght@400;700&display=swap">
<style>
  :root {
    --page-bg: #ffffff;
    --navy-deep: #16294a;
    --navy: #213d69;
    --navy-mid: #2d5389;
    --band-blue: #3f7cc4;
    --sky: #5d8fca;
    --ink-light: #ffffff;
    --ink-soft: #d9e3f0;
    --photo-grey: #9a9a9a;
    --bulb-tone: #7ea3cf;
    --label-bg: #1c3358;
  }
  * { box-sizing: border-box; margin: 0; padding: 0; }
  html, body {
    width: 1200px; height: 850px; overflow: hidden;
    background: var(--page-bg);
  }
  .cover-spread {
    position: absolute; left: 141px; top: 85px;
    width: 918px; height: 680px;
    display: flex;
    box-shadow: 0 6px 24px rgba(0,0,0,0.18);
  }
  .back-cover, .front-cover {
    position: relative; width: 450px; height: 680px;
    background: linear-gradient(180deg, var(--navy) 0%, var(--navy-mid) 45%, var(--navy) 80%, var(--navy-deep) 100%);
    color: var(--ink-light);
  }
  .spine {
    width: 18px; height: 680px;
    background: var(--navy-deep);
    display: flex; align-items: center; justify-content: center;
  }
  .spine-title {
    writing-mode: vertical-rl;
    font-family: "Tinos", serif; font-size: 11px; letter-spacing: 1px;
    text-transform: uppercase; color: var(--ink-light); white-space: nowrap;
  }

  /* Front */
  .front-title {
    position: absolute; top: 70px; left: 0; width: 100%;
    text-align: center; font-family: "Tinos", serif; font-weight: 400;
    font-size: 38px; line-height: 1.0; text-transform: uppercase;
    letter-spacing: 0.5px;
    text-shadow: 0 2px 3px rgba(0,0,0,0.4);
  }
  .subtitle-band {
    position: absolute; top: 208px; left: 0; width: 100%; height: 24px;
    background: var(--band-blue);
  }
  .subtitle-panel {
    position: absolute; top: 232px; left: 0; width: 100%; height: 88px;
    background: linear-gradient(180deg, var(--navy-mid), var(--sky));
  }
  .front-subtitle {
    position: absolute; top: 214px; left: 55px; width: 340px;
    text-align: center; font-family: "Arimo", sans-serif; font-size: 14px;
    line-height: 1.2; color: var(--ink-light);
  }
  .bulb-art {
    position: absolute; top: 345px; left: 185px; width: 80px; height: 100px;
    border-radius: 40px 40px 14px 14px;
    background: radial-gradient(circle at 50% 35%, var(--bulb-tone), transparent 70%);
  }
  .author-photo {
    position: absolute; top: 460px; left: 145px; width: 160px; height: 152px;
    background: linear-gradient(180deg, #6c7f99 0%, #3a4560 60%, #2a3142 100%);
  }
  .author-band {
    position: absolute; bottom: 0; left: 0; width: 100%; height: 78px;
    background: linear-gradient(180deg, rgba(22,41,74,0.85), var(--navy-deep));
    text-align: center; font-family: "Arimo", sans-serif; font-weight: 700;
  }
  .author-credit { margin-top: 8px; font-size: 17px; }
  .author-name { font-size: 28px; line-height: 1.2; }

  /* Back */
  .back-copy {
    position: absolute; top: 28px; left: 30px; width: 390px;
    font-family: "Arimo", sans-serif; font-size: 10.5px; line-height: 1.45;
    color: var(--ink-soft);
  }
  .back-copy p { margin-bottom: 12px; }
  .author-portrait {
    position: absolute; top: 480px; left: 30px; width: 90px; height: 112px;
    background: linear-gradient(180deg, #d8d8d8, var(--photo-grey));
  }
  .website-label {
    position: absolute; top: 480px; left: 135px;
    padding: 4px 10px; background: var(--label-bg);
    font-family: "Arimo", sans-serif; font-size: 13px; color: var(--ink-light);
  }
</style>
</head>
<body>
  <div class="cover-spread">
    <section class="back-cover">
      <div class="back-copy">
        <p>This path goes far beyond business! This is a book for the awakening builders who are shaping a kinder world, touching generations to come.</p>
        <p>Here is the chance to lead a richer life and business by seeing the quiet bond that exists between all beings. You will be invited to take your work to the next level and to grow your ties with yourself, your partner, family, friends and the wider Earth.</p>
        <p>Norman shares his own heartfelt stories and insights gained from years of working with teachers who hold old wisdom. He believes that when enough people look within, together we can make a lasting, positive mark on the world. Get ready to widen your view, reshape your business and build a life that serves all beings.</p>
        <p>Norman Quillfeather is a speaker, coach and best-selling author who has spoken to audiences in many countries. In this second book he invites you to look at the core of your true nature and how it shapes your journey as a builder. Leaders who work with him say that Norman's gift is helping them join purpose with profit.</p>
      </div>
      <div class="author-portrait" role="img" aria-label="Black and white photo of the author seated"></div>
      <div class="website-label">www.NormanQuillfeather.example</div>
    </section>

    <div class="spine"><span class="spine-title">The Harvest of Quiet Builders</span></div>

    <section class="front-cover">
      <h1 class="front-title">The Harvest<br>of Quiet<br>Builders</h1>
      <div class="subtitle-panel"></div>
      <div class="subtitle-band"></div>
      <p class="front-subtitle">How this ancient wisdom is helping billionaires, industry icons and entrepreneurs to be better leaders, increase impact and leave a legacy.</p>
      <div class="bulb-art" role="img" aria-label="Line illustration of a glowing light bulb"></div>
      <div class="author-photo" role="img" aria-label="Photo of a businessman in a suit looking upward"></div>
      <div class="author-band">
        <p class="author-credit">From the Best Selling Author of “Stillwater”</p>
        <p class="author-name">Norman Quillfeather</p>
      </div>
    </section>
  </div>
</body>
</html>
```